Design logo and business card.

Design and construct logo and card for my business which is an over seeing company of other smaller businesses. The companies name is ember4 business works. Im open to any ideas but i am looking for a very cool contemporary design with a very prestige feel. The card can be either single or double sided, Thank you and i will look forward to your submissions.

Business

• Company name, email, website, telephone, my name. Cool modern look with a prestige feel.

```html
<!DOCTYPE html>
<html lang="en">
<head>
<meta charset="utf-8">
<title>ember4 business works — business card</title>
<link href="https://fonts.googleapis.com/css2?family=Roboto:wght@300&display=swap" rel="stylesheet">
<style>
  :root {
    --stage: #3a3a3a;
    --card-base: #0b0b0c;
    --damask-light: #2a2a2d;
    --damask-mid: #18181a;
    --damask-dark: #070708;
    --brand-white: #f4f4f4;
    --accent-blue: #3fa9ea;
    --contact-grey: #a6a6a6;
    --icon-fill: #d0d0d0;
  }
  * { margin: 0; padding: 0; box-sizing: border-box; }
  html, body {
    width: 1200px;
    height: 1000px;
    overflow: hidden;
    background: var(--stage);
  }
  .canvas {
    position: relative;
    width: 1200px;
    height: 1000px;
    font-family: "Roboto", "Helvetica Neue", Arial, sans-serif;
    font-weight: 300;
  }
  .card {
    position: absolute;
    background: var(--card-base);
    overflow: hidden;
  }
  .card-front { left: 30px; top: 90px; width: 680px; height: 420px; }
  .card-back { left: 480px; top: 450px; width: 680px; height: 410px; }
  .card-pattern {
    position: absolute;
    inset: 0;
    background:
      radial-gradient(circle at 18% 25%, var(--damask-light) 0%, transparent 32%),
      radial-gradient(circle at 72% 20%, var(--damask-light) 0%, transparent 28%),
      radial-gradient(circle at 40% 78%, var(--damask-light) 0%, transparent 30%),
      radial-gradient(circle at 88% 72%, var(--damask-light) 0%, transparent 26%),
      radial-gradient(ellipse at 50% 50%, var(--damask-mid) 0%, var(--damask-dark) 85%);
  }
  .brand {
    position: absolute;
    display: flex;
    align-items: center;
    color: var(--brand-white);
    white-space: nowrap;
  }
  .brand-dot {
    border-radius: 50%;
    background: var(--accent-blue);
    flex: none;
  }
  .card-front .brand { left: 150px; top: 180px; font-size: 40px; gap: 18px; }
  .card-front .brand-dot { width: 40px; height: 40px; }
  .card-back .brand { left: 40px; top: 196px; font-size: 19px; gap: 10px; }
  .card-back .brand-dot { width: 20px; height: 20px; }
  .contact-list {
    position: absolute;
    left: 272px;
    top: 122px;
    list-style: none;
  }
  .contact-item {
    display: flex;
    align-items: center;
    gap: 16px;
    height: 39px;
    font-size: 28px;
    color: var(--contact-grey);
    letter-spacing: 0.2px;
  }
  .contact-icon { width: 28px; height: 28px; flex: none; }
</style>
</head>
<body>
<div class="canvas">

  <section class="card card-front">
    <div class="card-pattern" role="img" aria-label="Dark black floral damask pattern filling the card"></div>
    <div class="brand">
      <span class="brand-dot"></span>
      <span class="brand-name">ember4 business works</span>
    </div>
  </section>

  <section class="card card-back">
    <div class="card-pattern" role="img" aria-label="Dark black floral damask pattern filling the card"></div>
    <div class="brand">
      <span class="brand-dot"></span>
      <span class="brand-name">ember4 business works</span>
    </div>
    <ul class="contact-list">
      <li class="contact-item">
        <svg class="contact-icon" viewBox="0 0 26 26" aria-hidden="true">
          <circle cx="13" cy="8" r="5.5" fill="var(--icon-fill)"/>
          <path d="M3 25c0-6 4.5-10 10-10s10 4 10 10z" fill="var(--icon-fill)"/>
        </svg>
        <span>kai moren</span>
      </li>
      <li class="contact-item">
        <svg class="contact-icon" viewBox="0 0 26 26" aria-hidden="true">
          <circle cx="13" cy="13" r="11" fill="none" stroke="var(--icon-fill)" stroke-width="2"/>
          <ellipse cx="13" cy="13" rx="5" ry="11" fill="none" stroke="var(--icon-fill)" stroke-width="1.5"/>
          <line x1="2" y1="13" x2="24" y2="13" stroke="var(--icon-fill)" stroke-width="1.5"/>
        </svg>
        <span>ember4-works.com</span>
      </li>
      <li class="contact-item">
        <svg class="contact-icon" viewBox="0 0 26 26" aria-hidden="true">
          <rect x="2" y="5" width="22" height="16" fill="var(--icon-fill)"/>
          <path d="M2 5l11 9 11-9" fill="none" stroke="#555" stroke-width="1.5"/>
        </svg>
        <span>info@ember4-works.com</span>
      </li>
      <li class="contact-item">
        <svg class="contact-icon" viewBox="0 0 26 26" aria-hidden="true">
          <path d="M6 3l4 5-2.5 2.5c1.5 3 4 5.5 7 7L17 15l5 4-2.5 4C12 22 4 14 3 6z" fill="var(--icon-fill)"/>
        </svg>
        <span>+34 611 420 538</span>
      </li>
    </ul>
  </section>

</div>
</body>
</html>
```